Pre-workout label and Super Greens label for Brightmoor Nutrition Supplements

I need a label design for Club Brightmoor's 2 supplements. The first is a Pre-workout. The Pre-workout label needs to be 11.25 x 2.5 inches. This label will go on a black container. The second is a Super-Green. The Super-Green label should be 11.25 x 4.25 inches and will go on a white container. We have been selling these for a few years but the current labels are a little meh. I'd like something trendier and bolder. Must keep the Club Brightmoor branding. All the nurtition data must appear . I attached the current designs so you can know the flavors, nutrtional data etc. Thank you!
Updates

I can upload the Club Brightmoor logo! If anyone can tell me how to do that.

```html
<!DOCTYPE html>
<html lang="en">
<head>
<meta charset="utf-8">
<title>Brightmoor Nutrition – Pre-Workout Label</title>
<link href="https://fonts.googleapis.com/css2?family=Orbitron:wght@700;900&family=Oswald:wght@500;600&family=Montserrat:wght@400;500;600;700&family=Roboto:wght@400;500;700&display=swap" rel="stylesheet">
<style>
  :root{
    --ink:#0d0d0e;
    --panel:#151517;
    --red:#e4161b;
    --red-dark:#a80d10;
    --white:#ffffff;
    --silver-1:#5c5f63;
    --silver-2:#d9dbdd;
    --silver-3:#8b8e92;
    --muted:#cfcfcf;
    --page:#ffffff;
  }
  *{margin:0;padding:0;box-sizing:border-box}
  html,body{width:1200px;height:997px;overflow:hidden;background:var(--page)}
  .label{
    position:absolute;left:25px;top:370px;width:1150px;height:256px;
    background:radial-gradient(ellipse at 50% 50%,#1d1d20 0%,var(--ink) 75%);
    overflow:hidden;color:var(--white);font-family:"Montserrat",sans-serif;
  }
  .label-art{position:absolute;inset:0}
  .info-box{
    position:absolute;border:1px solid var(--red);border-radius:3px;background:var(--ink);
  }
  .directions{left:15px;top:16px;width:293px;height:176px;padding:10px 12px 0 12px}
  .box-heading{color:var(--red);font-weight:700;font-size:8.5px;line-height:10px;font-family:"Roboto",sans-serif}
  .box-copy{font-size:6px;line-height:8.5px;color:var(--white);text-align:justify;margin-bottom:3px;font-family:"Roboto",sans-serif}
  .disclaimer{
    position:absolute;left:40px;top:202px;width:245px;text-align:center;
    font-family:"Roboto",sans-serif;font-weight:700;font-size:6.6px;line-height:8.5px;
  }
  .brand{
    position:absolute;left:0;width:1150px;top:10px;text-align:center;
  }
  .brand-mark{display:inline-block;width:28px;height:28px;background:var(--red);border-radius:2px}
  .brand-name{
    display:block;margin-top:8px;font-family:"Oswald",sans-serif;font-weight:600;
    font-size:14px;letter-spacing:1.2px;color:var(--red);line-height:16px;
  }
  .product-name{
    position:absolute;left:0;width:1150px;top:94px;text-align:center;
    font-family:"Orbitron",sans-serif;font-weight:900;font-size:31px;line-height:36px;letter-spacing:1px;
    background:linear-gradient(180deg,#f4f4f4 0%,#bfc1c4 45%,#7d8085 55%,#e1e2e3 100%);
    -webkit-background-clip:text;background-clip:text;color:transparent;
  }
  .flavor{
    position:absolute;left:0;width:1150px;top:157px;text-align:center;
    font-family:"Orbitron",sans-serif;font-weight:900;font-size:11px;letter-spacing:1px;color:var(--red);
  }
  .benefit{position:absolute;top:175px;width:80px;text-align:center}
  .benefit svg{display:block;margin:0 auto}
  .benefit-name{font-family:"Oswald",sans-serif;font-weight:500;font-size:9.5px;line-height:11px;margin-top:3px}
  .benefit-source{font-size:5.6px;line-height:7px;color:var(--muted)}
  .benefit.energy{left:466px}
  .benefit.performance{left:536px}
  .benefit.strength{left:603px}
  .badge-dietary{
    position:absolute;left:410px;top:238px;width:150px;text-align:center;
    font-family:"Montserrat",sans-serif;font-weight:600;font-size:10px;letter-spacing:.3px;color:var(--white);
  }
  .net-contents{
    position:absolute;left:575px;top:239px;font-family:"Montserrat",sans-serif;font-weight:500;
    font-size:8.5px;letter-spacing:.6px;color:#1a1a1a;
  }
  .facts{left:838px;top:16px;width:295px;height:176px;padding:2px 5px 0 3px;font-family:"Roboto",sans-serif}
  .facts-title{font-size:11.5px;font-weight:700;line-height:13px}
  .facts-meta{font-size:6px;line-height:7px}
  .facts-table{width:100%;border-collapse:collapse;margin-top:2px;font-size:5.4px}
  .facts-table th{font-weight:700;font-size:6px;text-align:left;border-top:2px solid var(--white);border-bottom:1px solid var(--white);padding:1px 0}
  .facts-table td{border-bottom:1px solid var(--white);padding:1.4px 0;line-height:7px}
  .facts-table .col-amount{width:39%}
  .facts-table .col-dv{width:12%;text-align:right;font-weight:700}
  .facts-table tr:last-child td{border-bottom:2px solid var(--white)}
  .facts-foot{font-size:5.4px;margin-top:3px}
  .other-ingredients{
    position:absolute;left:838px;width:295px;top:202px;text-align:center;
    font-family:"Roboto",sans-serif;font-style:italic;font-size:6.2px;line-height:7.5px;
  }
  .formulator{
    position:absolute;left:838px;width:295px;top:222px;text-align:center;
    font-family:"Montserrat",sans-serif;font-weight:700;font-size:6.6px;
  }
</style>
</head>
<body>
<section class="label" aria-label="Brightmoor Nutrition Pre-Workout label">
  <svg class="label-art" width="1150" height="256" viewBox="0 0 1150 256" aria-hidden="true">
    <defs>
      <linearGradient id="silver" x1="0" x2="1" y1="0" y2="0">
        <stop offset="0" stop-color="#4e5155"/>
        <stop offset=".3" stop-color="#d7d9db"/>
        <stop offset=".55" stop-color="#7f8287"/>
        <stop offset=".8" stop-color="#e4e5e6"/>
        <stop offset="1" stop-color="#6b6e72"/>
      </linearGradient>
      <linearGradient id="band" x1="0" x2="0" y1="0" y2="1">
        <stop offset="0" stop-color="#2b2c2f"/>
        <stop offset=".5" stop-color="#0b0b0c"/>
        <stop offset="1" stop-color="#2b2c2f"/>
      </linearGradient>
    </defs>
    <!-- top rail -->
    <rect x="0" y="81" width="1150" height="2" fill="var(--red)"/>
    <polygon points="350,85 440,78 640,76 680,85" fill="url(#silver)" opacity=".8"/>
    <polygon points="610,76 640,76 660,83 628,83" fill="var(--red)"/>
    <polygon points="625,72 695,72 710,83 640,83" fill="var(--red)"/>
    <!-- title band -->
    <rect x="0" y="90" width="1150" height="42" fill="url(#band)"/>
    <rect x="0" y="88" width="1150" height="1" fill="#3a3b3e"/>
    <rect x="0" y="133" width="1150" height="1" fill="#3a3b3e"/>
    <!-- lower rail -->
    <rect x="0" y="140" width="1150" height="1.5" fill="#d8d8d8"/>
    <polygon points="470,142 540,136 640,136 680,142" fill="url(#silver)" opacity=".7"/>
    <polygon points="545,138 610,138 620,145 535,145" fill="var(--red)"/>
    <!-- bottom band -->
    <rect x="0" y="235" width="1150" height="21" fill="url(#silver)"/>
    <rect x="0" y="233" width="1150" height="1.5" fill="var(--red)"/>
    <polygon points="412,236 575,236 562,256 398,256" fill="var(--red)"/>
    <polygon points="405,236 412,236 398,256 391,256" fill="var(--ink)"/>
    <polygon points="575,236 582,236 569,256 562,256" fill="var(--ink)"/>
  </svg>

  <div class="info-box directions">
    <p class="box-heading">Directions:</p>
    <p class="box-copy">Use on training days only. Mix 1 scoop with 6–8 oz of cold water 15–30 minutes prior to training.</p>
    <p class="box-heading">Warning:</p>
    <p class="box-copy">Not intended for use by persons under age 18. Do not exceed recommended dose. Do not consume synephrine or caffeine from other sources, including but not limited to: coffee, tea, soda, and other dietary supplements or medications containing phenylephrine or caffeine. Contains caffeine. Use in a 12 week on, 2 week off pattern. Consult your physician prior to use if you are pregnant or nursing, or if you are taking medication, including but not limited to: MAOI inhibitors, antidepressants, aspirin, non-steroidal, anti-inflammatory drugs or products containing phenylephrine, ephedrine, pseudoephedrine, or other stimulants. Consult your physician prior to use if you have a medical condition, including but not limited to: heart, liver, kidney, or thyroid disease, cardiac arrhythmia, recurrent headaches, enlarged prostate or glaucoma. Discontinue use 2 weeks prior to surgery or if you experience rapid heartbeat, dizziness, severe headaches, or shortness of breath. This product DOES NOT contain ingredients banned by certain sports organizations.</p>
  </div>

  <p class="disclaimer">*These statements have not been evaluated by the Food and Drug Administration. This product is not intended to diagnose, treat, cure or prevent any disease.</p>

  <div class="brand">
    <span class="brand-mark" aria-hidden="true"></span>
    <span class="brand-name">BRIGHTMOOR NUTRITION</span>
  </div>

  <h1 class="product-name">PRE-WORKOUT</h1>
  <p class="flavor">WATERMELON SUGAR</p>

  <div class="benefit energy">
    <svg width="26" height="28" viewBox="0 0 26 28" aria-hidden="true">
      <path d="M1 1h24v17l-12 9-12-9z" fill="var(--red)" stroke="#ff5a5e" stroke-width="1"/>
      <circle cx="13" cy="13" r="7" fill="none" stroke="#fff" stroke-width="1.6"/>
      <path d="M14 8l-4 6h3l-1 4 4-6h-3z" fill="#fff"/>
    </svg>
    <p class="benefit-name">ENERGY</p>
    <p class="benefit-source">(Caffeine)</p>
  </div>
  <div class="benefit performance">
    <svg width="26" height="28" viewBox="0 0 26 28" aria-hidden="true">
      <path d="M1 1h24v17l-12 9-12-9z" fill="var(--red)" stroke="#ff5a5e" stroke-width="1"/>
      <circle cx="13" cy="13" r="7" fill="none" stroke="#fff" stroke-width="1.6" stroke-dasharray="4 1.5"/>
      <path d="M13 13l4-3" stroke="#fff" stroke-width="1.6" stroke-linecap="round"/>
      <circle cx="13" cy="13" r="1.5" fill="#fff"/>
    </svg>
    <p class="benefit-name">PERFORMANCE</p>
    <p class="benefit-source">(Beta-alanine)</p>
  </div>
  <div class="benefit strength">
    <svg width="26" height="28" viewBox="0 0 26 28" role="img" aria-label="Strength badge icon">
      <path d="M1 1h24v17l-12 9-12-9z" fill="var(--red)" stroke="#ff5a5e" stroke-width="1"/>
      <rect x="7" y="7" width="12" height="11" rx="2" fill="#f2f2f2"/>
    </svg>
    <p class="benefit-name">STRENGTH</p>
    <p class="benefit-source">(Creatine)</p>
  </div>

  <p class="badge-dietary">DIETARY SUPPLEMENT</p>
  <p class="net-contents">30 SERVINGS 240G (8.5OZ)</p>

  <div class="info-box facts">
    <p class="facts-title">Supplement Facts</p>
    <p class="facts-meta">Serving Size: 1 Scoop (8 g)</p>
    <p class="facts-meta">Servings per Container: 30</p>
    <table class="facts-table">
      <thead><tr><th></th><th class="col-amount">Amount per Serving</th><th class="col-dv">%DV</th></tr></thead>
      <tbody>
        <tr><td>Vitamin C (Ascorbic Acid)</td><td>250mg</td><td class="col-dv">278%</td></tr>
        <tr><td>Vitamin B6 (as Pyridoxal-5’-Phosphate)</td><td>0.035 mg</td><td class="col-dv">2%</td></tr>
        <tr><td>Folate</td><td>250 mcg DFE (150 mcg Folic Acid)</td><td class="col-dv">63%</td></tr>
        <tr><td>Vitamin B12 (as Methylcobalamin)</td><td>20 mcg</td><td class="col-dv">833%</td></tr>
        <tr><td>Calcium (as Calcium Silicate)</td><td>18.30 mg</td><td class="col-dv">1%</td></tr>
        <tr><td>Beta-Alanine</td><td>1.5 g</td><td class="col-dv">†</td></tr>
        <tr><td>Creatine Monohydrate</td><td>1 g</td><td class="col-dv">†</td></tr>
        <tr><td>L-Arginine Alpha-Ketoglutarate</td><td>1 g</td><td class="col-dv">†</td></tr>
        <tr><td>L-Citrulline Malate</td><td>1 g</td><td class="col-dv">†</td></tr>
        <tr><td>N-Acetyl L-Tyrosine</td><td>500 mg</td><td class="col-dv">†</td></tr>
        <tr><td>Caffeine Anhydrous</td><td>250 mg</td><td class="col-dv">†</td></tr>
        <tr><td>Synephrine HCl</td><td>30 mg</td><td class="col-dv">†</td></tr>
      </tbody>
    </table>
    <p class="facts-foot">† Daily Value (DV) not established</p>
  </div>

  <p class="other-ingredients">Other Ingredients: Citric Acid, Pineapple Fruit Juice Powder, Silicon Dioxide, Natural and Artificial Flavors, Acesulfame Potassium, Sucralose, and FD&amp;C Red #40.</p>
  <p class="formulator">Formulated by: Club Brightmoor, 88 Orchard Rd Alder, WY 82000 (555) 014-2290</p>
</section>
</body>
</html>
```